Website for Barlow Fabrication & Building Ltd

General Note to all.

1. Piling and gas works are separate areas of work and should not be put together.
- the marine section should really be the piling works and should have all the barges/water piles etc.
- the gas section should have the big silo looking thing

2. I would like to add in Specialist Onsite Labour and Management in the 'our services' section. The would include the Supervisors, Coded Welders, Site Fitters and Crane and Rig Crews etc.

3. I did like it how someone had use the BFB header logo as the top of the webpage with the individual tabs above and the website starting below. Please remove the VAT number and phone number from this section.

4. I also liked how one designer incorporate the orange line with spark (from the logo) as a page separator representing the welding part of the business

5. Add in a Mission Statement - To go above and beyond in to ensure our clients projects are delivered safely, ahead of schedule, in any environment for the benefit of not only our customers but also our employees and communities we work in.

6. Add in Business Objectives -BFB is on a mission to be one of the leading contractors in UK to supply All Site Labour - ranging from Site Management, fully Coded Welders, Site Fitters and Crane and Rig Crews.

7. I am happy for you to add in photos that are not ours for the thumbs nails for the our services. ie a colourful welding pics/cool tunnelling pic etc - just make sure I will not get done for copy write infringements

8. I would like a some type of 'contact us' field or 'request a consultation' section.

9. Please confirm if the webpages you create will be compatible for both desktop and mobile app and how difficult it will be to update personally once it is live.

10. You have all done very well and have thus far been very impressed with what you have produced. I gave a very vague brief as I was not entirely sure how you would go about making something with very little information. Some of the designs look very professional.

11. I'm not sure how once I choose the winning design how that then transfers over to my domain? Perhaps someone can help me with that? I will also be looking for a web hosting platform so feel free to provide this information.

After using Sketch hive for successful getting a professional logo for the company I'm giving the web design option a go.

I am looking for a professional website for the above civil construction company.

The company director has many years experience in Marine, tunnelling, conveyors, stadium construction gas and piling works including piling works for coal ports, bridges and tunnels.

The company currently provide 20+ skilled and experienced guys from all trades (supervisors, coded welders, fitters, crane drivers and crane supervisors, rigglers, slingers and piling operatives) on the Corran Shoreline project in London - London's new super sewer. Most of this work is off barges carrying cranes (upto 600T and drill rigs).

As we are looking to expand and get more subcontracts we need a web presence to say who we are and what we do.

I'll include the 2 company logos we currently use below

I have included an info doc with pics you may or may not use.

Target Market(s)

Mainly other large construction companies and potential subcontractors

Industry/Entity Type

Construction Company

Coding

Coded - Design and coding required

Font styles to use
Sans Serif

Colors
0655a3
f37122
ffffff

Requirements
Must have
• Few tabs
• Simple to use/update but still professional look
• The challenge will be making the website look professional with not much available content.
Should not have
• No residential house building

```html
<!DOCTYPE html>
<html lang="en">
<head>
<meta charset="utf-8">
<title>Barlow Fabrication &amp; Building Ltd</title>
<link href="https://fonts.googleapis.com/css2?family=Open+Sans:wght@400;600;700&family=Montserrat:wght@400;500&display=swap" rel="stylesheet">
<style>
:root{
  --orange:#e8591c;
  --blue:#0b3f8f;
  --navy:#16234a;
  --ink:#333;
  --muted:#555;
  --grey-bg:#f3f3f3;
  --footer:#2b2b2b;
  --line:#d6d6d6;
  --white:#fff;
}
*{margin:0;padding:0;box-sizing:border-box}
html,body{width:1200px;height:2362px;overflow:hidden;background:var(--white)}
body{font-family:"Open Sans",Arial,sans-serif;color:var(--ink);position:relative}

.site-header{position:absolute;top:0;left:0;width:1200px;height:142px}
.brand{position:absolute;left:132px;top:26px;display:flex;align-items:center;gap:10px;color:var(--navy);font-weight:700}
.brand-mark{width:30px;height:30px;border-radius:50%;background:var(--orange)}
.brand-name{line-height:1}
.brand-name b{display:block;font-size:50px;letter-spacing:1px}
.brand-name span{display:block;font-size:11px;letter-spacing:.5px;margin-top:4px}
.main-nav{position:absolute;right:132px;top:100px;display:flex;gap:34px;font-family:"Montserrat",sans-serif;font-size:13px}
.main-nav a{color:var(--ink);text-decoration:none}
.main-nav a.active{color:var(--orange)}

.spark-rule{position:absolute;left:0;width:1200px;height:14px}
.spark-rule.header-rule{top:132px}

.hero{position:absolute;top:142px;left:0;width:1200px;height:472px;background:linear-gradient(180deg,#5f8fd2 0%,#9cbde6 38%,#c98f5a 62%,#6b4a36 78%,#2f3c55 100%)}
.hero-title{position:absolute;top:50px;width:100%;text-align:center;font-size:33px;font-weight:600;color:#2e2e2e}
.hero-arrow{position:absolute;top:220px;width:36px;height:36px;border-radius:50%;background:var(--orange);border:2px solid #fff;display:flex;align-items:center;justify-content:center}
.hero-arrow.prev{left:46px}.hero-arrow.next{right:46px}

.welcome{position:absolute;top:636px;left:130px;width:940px;text-align:center}
.section-title{font-size:43px;font-weight:700;color:var(--orange);line-height:1.2}
.welcome p{font-size:13px;line-height:23px;color:var(--muted);margin-top:8px}

.goals{position:absolute;top:800px;left:130px;width:940px;display:grid;grid-template-columns:1fr 1fr;gap:28px}
.goal h3{font-size:15px;font-weight:700;color:var(--blue);line-height:20px;border-left:3px solid var(--orange);padding-left:8px}
.goal p{font-size:12.5px;line-height:19px;color:var(--muted);margin-top:4px}

.skyline{position:absolute;left:0;width:1200px;height:66px}
.skyline.top{top:924px;background:linear-gradient(180deg,rgba(11,63,143,0) 0%,rgba(11,63,143,.4) 50%,var(--blue) 100%)}

.services{position:absolute;top:990px;left:0;width:1200px;height:312px;background:var(--blue)}
.service{position:absolute;top:62px;width:160px;margin-left:-80px;text-align:center;color:#fff}
.service-circle{width:128px;height:128px;border-radius:50%;background:#fff;margin:0 auto;display:flex;align-items:center;justify-content:center}
.service-icon{width:58px;height:58px;border-radius:8px;background:#d7e2f3}
.service h3{font-size:16px;font-weight:600;line-height:20px;margin-top:12px}

.projects{position:absolute;top:1302px;left:0;width:1200px;height:614px;background:var(--grey-bg)}
.projects .section-title{position:absolute;top:80px;width:100%;text-align:center}
.project-grid{position:absolute;left:133px;top:148px;width:935px;display:grid;grid-template-columns:repeat(3,1fr);gap:9px 8px}
.project-tile{height:183px}
.t1{background:linear-gradient(180deg,#5d8fe0 0%,#8fb2ea 55%,#4e6a3c 72%,#6a6d72 100%)}
.t2{background:linear-gradient(180deg,#4b7fd6 0%,#86a9e0 55%,#3b3a36 75%,#615a4b 100%)}
.t3{background:linear-gradient(180deg,#cfd3d0 0%,#4a4a44 40%,#2b2c26 100%)}
.t4{background:linear-gradient(180deg,#7a7a72 0%,#bdbdb2 35%,#4f4d45 100%)}
.t5{background:linear-gradient(180deg,#9eb6d6 0%,#c03a30 45%,#3a3a3a 100%)}
.t6{background:linear-gradient(180deg,#6f93c9 0%,#a45a3a 50%,#3e3a30 100%)}
.grid-arrow{position:absolute;top:325px}
.grid-arrow.prev{left:54px}.grid-arrow.next{right:54px}

.clients{position:absolute;top:1975px;left:0;width:1200px;text-align:center}
.client-row{display:flex;justify-content:space-between;align-items:center;width:935px;margin:22px auto 0;font-size:16px;font-weight:700;color:var(--navy)}

.consultation{position:absolute;top:2112px;left:133px;width:935px;display:flex;align-items:center;gap:12px}
.consultation h2{font-size:18px;font-weight:700;color:var(--orange);white-space:nowrap;margin-right:6px}
.consultation input{flex:1;height:36px;border:1px solid var(--line);padding:0 10px;font-family:inherit;font-size:13px;color:var(--ink);background:#fff}
.consultation button{height:36px;padding:0 22px;border:0;background:var(--orange);color:#fff;font-family:inherit;font-size:13px;font-weight:600}

.skyline.bottom{top:2200px;height:70px;background:linear-gradient(180deg,rgba(43,43,43,0) 0%,rgba(43,43,43,.4) 50%,var(--footer) 100%)}
.site-footer{position:absolute;top:2270px;left:0;width:1200px;height:92px;background:var(--footer);color:#bbb}
.footer-links{position:absolute;left:133px;top:22px;font-size:10px}
.footer-links a{color:#ccc;text-decoration:none}
.footer-links i{font-style:normal;margin:0 6px}
.copyright{position:absolute;left:133px;top:50px;font-size:10px}
.social{position:absolute;right:132px;top:30px;display:flex;gap:6px}
.social span{width:24px;height:24px;border-radius:50%;background:#2d8ee0}
</style>
</head>
<body>
<header class="site-header">
  <div class="brand"><span class="brand-mark"></span><div class="brand-name"><b>BFB</b><span>BARLOW FABRICATION &amp; BUILDING</span></div></div>
  <nav class="main-nav"><a class="active" href="#">Home</a><a href="#">About Us</a><a href="#">Services</a><a href="#">Projects</a><a href="#">Contact Us</a></nav>
</header>

<section class="hero" role="img" aria-label="Piling barge with crane platform on a river at sunset">
  <h1 class="hero-title">Vestibulum condimentum, risus ut posuere</h1>
  <span class="hero-arrow prev"><svg width="12" height="14" viewBox="0 0 12 14"><path d="M9 1 3 7l6 6" fill="none" stroke="#fff" stroke-width="3"/></svg></span>
  <span class="hero-arrow next"><svg width="12" height="14" viewBox="0 0 12 14"><path d="M3 1l6 6-6 6" fill="none" stroke="#fff" stroke-width="3"/></svg></span>
</section>

<svg class="spark-rule header-rule" viewBox="0 0 1200 14" aria-hidden="true">
  <rect x="0" y="9" width="1200" height="3" fill="#e8591c"/>
  <polygon points="900,0 903,8 911,10.5 903,13 900,14 897,13 889,10.5 897,8" fill="#e8591c"/>
</svg>

<section class="welcome">
  <h2 class="section-title">Welcome</h2>
  <p>Barlow Fabrication &amp; Building has over 15years experience working in the civil construction industry. We are currently working on the Corran Shoreline project in London. We are subcontracted to Vantor Hallam Drake Joint Venture and provide a highly skilled workforce across many of the Corran Shoreline sites. We have a strong history in the piling industry both in the UK and in Australia. Notable projects include working on K7 and K10 Coal Berths with Hallam Drake and Kellsworth Bridge over the Warrabel River for Stonewharf in NSW Australia.</p>
</section>

<section class="goals">
  <div class="goal">
    <h3>Mission Statement</h3>
    <p>To go above and beyond to ensure our clients' projects are delivered safely, ahead of schedule, in any environment, for the benefit of not only our customers but also our employees and the communities we work in.</p>
  </div>
  <div class="goal">
    <h3>Business Objectives</h3>
    <p>BFB is on a mission to be one of the leading contractors in the UK to supply all site labour, ranging from Site Management and fully Coded Welders to Site Fitters and Crane and Rig Crews.</p>
  </div>
</section>

<div class="skyline top" role="img" aria-label="Silhouette of harbour cranes and industrial skyline"></div>
<section class="services">
  <div class="service" style="left:197px"><div class="service-circle"><span class="service-icon" role="img" aria-label="Offshore piling rig icon"></span></div><h3>Marine and<br>piling</h3></div>
  <div class="service" style="left:359px"><div class="service-circle"><span class="service-icon" role="img" aria-label="Tunnel icon"></span></div><h3>Tunnelling</h3></div>
  <div class="service" style="left:520px"><div class="service-circle"><span class="service-icon" role="img" aria-label="Site worker icon"></span></div><h3>Skill Labour<br>Supply</h3></div>
  <div class="service" style="left:680px"><div class="service-circle"><span class="service-icon" role="img" aria-label="Drill rig icon"></span></div><h3>Stadium<br>Construction</h3></div>
  <div class="service" style="left:842px"><div class="service-circle"><span class="service-icon" role="img" aria-label="Coal wagon icon"></span></div><h3>Coal Ports</h3></div>
  <div class="service" style="left:1003px"><div class="service-circle"><span class="service-icon" role="img" aria-label="Bridge icon"></span></div><h3>Bridges</h3></div>
</section>

<section class="projects">
  <h2 class="section-title">Projects</h2>
  <svg class="grid-arrow prev" width="14" height="24" viewBox="0 0 14 24"><path d="M12 2 2 12l10 10" fill="none" stroke="#777" stroke-width="2"/></svg>
  <div class="project-grid">
    <div class="project-tile t1" role="img" aria-label="Crane barge on a river"></div>
    <div class="project-tile t2" role="img" aria-label="Piling rig on a barge"></div>
    <div class="project-tile t3" role="img" aria-label="Tunnel interior with lighting"></div>
    <div class="project-tile t4" role="img" aria-label="Steel piles in water beside a quay"></div>
    <div class="project-tile t5" role="img" aria-label="Large red crane on site"></div>
    <div class="project-tile t6" role="img" aria-label="Pile installation at a barge edge"></div>
  </div>
  <svg class="grid-arrow next" width="14" height="24" viewBox="0 0 14 24"><path d="M2 2l10 10L2 22" fill="none" stroke="#777" stroke-width="2"/></svg>
</section>

<section class="clients">
  <h2 class="section-title">Clients</h2>
  <div class="client-row"><span>Shoreline</span><span>Fenlo</span><span>Corbel</span><span>Stonewharf</span><span>Hallam Drake</span><span>Brimley</span><span>Farrowgate</span><span>Southbore</span></div>
</section>

<form class="consultation">
  <h2>Request a consultation</h2>
  <input type="text" placeholder="Name">
  <input type="email" placeholder="Email">
  <input type="text" placeholder="Project details">
  <button type="button">Send</button>
</form>

<div class="skyline bottom" role="img" aria-label="Silhouette of harbour cranes and industrial skyline"></div>
<footer class="site-footer">
  <div class="footer-links"><a href="#">Home</a><i>|</i><a href="#">About Us</a><i>|</i><a href="#">Services</a><i>|</i><a href="#">Projects</a><i>|</i><a href="#">Contact Us</a></div>
  <div class="copyright">Copyright © 2018 Barlow Fabrication &amp; Building. All rights reserved.</div>
  <div class="social"><span aria-label="Social link one"></span><span aria-label="Social link two"></span></div>
</footer>
</body>
</html>
```